Communication and Marketing agency needs a new presentation card

We are a group of communication and marketing agencies specialized in companies that are in the logistics and industrial sector. The head agency is TELVANO Grupo and the group consists of 4 agencies: TELVANO Media, TELVANO Digital, TELVANO Research and DifundeEnPantalla. We hace 4 offices in Spain (Madrid, Barcelona, Valencia and Murcia). We are looking for a clean and attractive design that transmits our experience, brand presence in the market and knowledge to those who receive the card.It has to maintain the colors of the logo that is attached.
Target Market(s)
logistics and industrial sector
Marketing department
Contact Information for Business Card
Clean and attractive design

```html
<!DOCTYPE html>
<html lang="en">
<head>
<meta charset="utf-8">
<title>TELVANO Grupo – Business Card</title>
<link rel="stylesheet" href="https://fonts.googleapis.com/css2?family=Open+Sans:wght@400;600;700&display=swap">
<style>
  :root {
    --brand-red: #b01c27;
    --brand-grey: #4f4c4a;
    --band-white: #f2f1f0;
    --circle-white: #f7f6f5;
    --circle-edge: #dedbd8;
    --text-light: #ffffff;
    --text-dark: #55524f;
    --page-bg: #e8e6e3;
  }
  * { margin: 0; padding: 0; box-sizing: border-box; }
  html, body {
    width: 1200px; height: 900px; overflow: hidden;
    background: var(--page-bg);
    font-family: "Open Sans", Arial, sans-serif;
  }
  .business-card {
    position: absolute; left: 120px; top: 154px;
    width: 960px; height: 592px;
    overflow: hidden;
    box-shadow: 0 12px 30px rgba(0,0,0,0.18);
  }
  .card-background { position: absolute; inset: 0; }

  .holder {
    position: absolute; left: 56px; top: 62px; color: var(--text-light);
  }
  .holder-name { font-size: 35px; font-weight: 700; letter-spacing: 0.5px; line-height: 1.2; }
  .holder-role { font-size: 26px; font-weight: 400; line-height: 1.3; }

  .agency-grid {
    position: absolute; left: 40px; top: 232px;
    width: 360px;
    display: grid; grid-template-columns: 175px 175px; grid-auto-rows: 60px;
    row-gap: 18px; column-gap: 10px;
  }
  .agency { text-align: right; font-weight: 600; line-height: 1.05; }
  .agency-name { display: block; font-size: 29px; letter-spacing: 0.5px; }
  .agency-unit { display: block; font-size: 17px; }
  .agency--grey { color: var(--text-dark); }
  .agency--red { color: var(--brand-red); }
  .agency--compact { padding-top: 6px; }
  .agency--compact .agency-name { font-size: 20px; letter-spacing: 0; line-height: 1.15; }

  .contact-list {
    position: absolute; left: 56px; top: 413px;
    list-style: none; color: var(--text-light);
    font-size: 26px; line-height: 35px;
  }
  .contact-list li { display: flex; align-items: center; gap: 10px; }
  .contact-icon { width: 22px; height: 22px; flex: none; fill: var(--text-light); }

  .group-mark {
    position: absolute; left: 450px; top: 238px; width: 430px;
    display: flex; flex-direction: column; align-items: center;
    color: var(--brand-red); font-weight: 600;
  }
  .group-name { font-size: 78px; letter-spacing: 4px; line-height: 1; }
  .group-unit { font-size: 46px; line-height: 1.1; align-self: flex-end; margin-right: 12px; }
</style>
</head>
<body>
  <div class="business-card">
    <svg class="card-background" width="960" height="592" viewBox="0 0 960 592" aria-hidden="true">
      <rect x="0" y="0" width="960" height="592" fill="var(--brand-grey)"/>
      <rect x="0" y="0" width="960" height="294" fill="var(--brand-red)"/>
      <rect x="0" y="213" width="700" height="170" fill="var(--band-white)"/>
      <circle cx="685" cy="297" r="257" fill="var(--circle-edge)"/>
      <circle cx="685" cy="297" r="251" fill="var(--circle-white)"/>
    </svg>

    <div class="holder">
      <p class="holder-name">LUCAS ARVENTO</p>
      <p class="holder-role">Managing Director</p>
    </div>

    <div class="agency-grid">
      <p class="agency agency--grey"><span class="agency-name">TELVANO</span><span class="agency-unit">Research</span></p>
      <p class="agency agency--grey"><span class="agency-name">TELVANO</span><span class="agency-unit">Digital</span></p>
      <p class="agency agency--red"><span class="agency-name">TELVANO</span><span class="agency-unit">Media</span></p>
      <p class="agency agency--red agency--compact"><span class="agency-name">DIFUNDE</span><span class="agency-name">ENPANTALLA</span></p>
    </div>

    <ul class="contact-list">
      <li>
        <svg class="contact-icon" viewBox="0 0 24 24" aria-hidden="true"><path d="M3 9c0-3 4-5 9-5s9 2 9 5v2h-5V9H8v2H3z"/><path d="M6 12h12l2 8H4z"/></svg>
        055-987 321 640
      </li>
      <li>
        <svg class="contact-icon" viewBox="0 0 24 24" aria-hidden="true"><path d="M7 2h10a1 1 0 0 1 1 1v18a1 1 0 0 1-1 1H7a1 1 0 0 1-1-1V3a1 1 0 0 1 1-1zm1 3v13h8V5z"/></svg>
        055-987 321 640
      </li>
      <li>
        <svg class="contact-icon" viewBox="0 0 24 24" aria-hidden="true"><path d="M2 5h20v14H2zm2 2v.4l8 5.5 8-5.5V7z"/></svg>
        info@telvanogrupo.com
      </li>
      <li>
        <svg class="contact-icon" viewBox="0 0 24 24" aria-hidden="true"><circle cx="12" cy="12" r="10"/></svg>
        www.telvanogrupo.com
      </li>
    </ul>

    <div class="group-mark">
      <span class="group-name">TELVANO</span>
      <span class="group-unit">Grupo</span>
    </div>
  </div>
</body>
</html>
```